Business card design

I need my logo on this card, things I need the card to have on it
licensed and insured.
owner operators Milo & Trent Halvorsen
my phone number 5083716254
Disaster Recovery, Storm Damage Restoration, Proactive Disaster Plan Management, Roof Repair/Restoration Structural Repair and Reconstruction, Emergency Boarding and Tarping Service, Perimeter Fencing, Emergency Tree Removal,

```html
<!DOCTYPE html>
<html lang="en">
<head>
<meta charset="UTF-8">
<title>Halvorsen's Construction L.L.C — Business Card</title>
<link href="https://fonts.googleapis.com/css2?family=Mulish:wght@400;500&display=swap" rel="stylesheet">
<style>
  :root {
    --brand-blue: #1b96e6;
    --ink: #111111;
    --card-border: #2a2a2a;
    --paper: #ffffff;
  }
  * { margin: 0; padding: 0; box-sizing: border-box; }
  html, body {
    width: 987px;
    height: 1200px;
    overflow: hidden;
    background: var(--paper);
    font-family: "Mulish", sans-serif;
  }
  .sheet {
    position: relative;
    width: 987px;
    height: 1200px;
  }
  .card {
    position: absolute;
    left: 0;
    width: 987px;
    height: 565px;
    border: 1px solid var(--card-border);
    background: var(--paper);
    display: flex;
    flex-direction: column;
    align-items: center;
    text-align: center;
  }
  .card--front { top: 0; }
  .card--back { top: 634px; }

  .brand-mark {
    background: var(--brand-blue);
  }
  .brand-name {
    color: var(--brand-blue);
    font-weight: 400;
    line-height: 1;
  }
  .brand-name__primary { display: block; }
  .brand-name__secondary { display: block; }

  /* Front */
  .card--front .brand-mark {
    width: 96px;
    height: 96px;
    margin-top: 50px;
  }
  .card--front .brand-name { margin-top: 36px; }
  .card--front .brand-name__primary {
    font-size: 48px;
    letter-spacing: 1px;
  }
  .card--front .brand-name__secondary {
    font-size: 14px;
    letter-spacing: 10.5px;
    margin-top: 8px;
    margin-right: -10.5px;
  }
  .owners {
    font-size: 45px;
    font-weight: 400;
    color: var(--ink);
    margin-top: 52px;
    line-height: 1;
  }
  .phone {
    font-size: 39px;
    font-weight: 500;
    color: var(--ink);
    margin-top: 26px;
    letter-spacing: 0.5px;
    line-height: 1;
  }
  .services {
    list-style: none;
    margin-top: 50px;
    font-size: 17.5px;
    line-height: 21px;
    color: var(--ink);
  }

  /* Back */
  .card--back .brand-mark {
    width: 196px;
    height: 196px;
    margin-top: 110px;
  }
  .card--back .brand-name { margin-top: 92px; }
  .card--back .brand-name__primary {
    font-size: 80px;
    letter-spacing: 1px;
  }
  .card--back .brand-name__secondary {
    font-size: 24px;
    letter-spacing: 19px;
    margin-top: 14px;
    margin-right: -19px;
  }
</style>
</head>
<body>
<main class="sheet">
  <section class="card card--front" aria-label="Card front">
    <div class="brand-mark" aria-hidden="true"></div>
    <p class="brand-name">
      <span class="brand-name__primary">HALVORSEN'S</span>
      <span class="brand-name__secondary">CONSTRUCTION L.L.C</span>
    </p>
    <h1 class="owners">Milo &amp; Trent Halvorsen</h1>
    <p class="phone">5083716254</p>
    <ul class="services">
      <li>Disaster Recovery • Storm Damage Restoration • Proactive Disaster Plan Management</li>
      <li>Roof Repair/Restoration • Structural Repair and Reconstruction • Emergency Boarding and Tarping Service</li>
      <li>Perimeter Fencing • Emergency Tree Removal</li>
    </ul>
  </section>

  <section class="card card--back" aria-label="Card back">
    <div class="brand-mark" aria-hidden="true"></div>
    <p class="brand-name">
      <span class="brand-name__primary">HALVORSEN'S</span>
      <span class="brand-name__secondary">CONSTRUCTION L.L.C</span>
    </p>
  </section>
</main>
</body>
</html>
```